Design a modern, classy & professional business card for an online real estate agency, specializing in medium-luxury properties in Thailand and later in Singapore and UK.

Possible design ideas so far: (not essential)

- curved corner(s) to the card, white on front & turquoise on back or visa versa.

- front of card - clear and simple, company name in metallic grey/monochrome, logo graphic & company name on front in spot UV or embossed/debossed effect.

- back of card - large, close-cropped, 'ghost' patterns of the C-shaped curves of logo, or company name repeated on back of card in spot UV.

Target Market(s)

- young to middle-aged professionals mainly (but ideally should design should suit all)

- UK, US,EU,AUS & ASIAN mainly (but ideally should design should suit all countries)

Industry/Entity Type

Real Estate

Requirements
Must have
• THEME:
- Luxurious & Modern
- Clean & striking
- Unique & creative

INFO:
- Logo & company name on front
- Contact details on back:

Tobias Hennlund
Managing Director

www.velmontestates.asia
www.velmontestates.co.uk

Tel: 083-274-6159
email: tobias@velmontestates.asia

(contact details can be displayed in any order as suites design.)

Nice to have
• - curved corner(s) to the card, white on front & turquoise on back or visa versa.

Should not have
• - No generic images of properties, palm trees/coconut trees etc.

- No other other bold colors, except for main turquoise, grey, metallic white & black theme.

- No obvious business card templates

```html
<!DOCTYPE html>
<html lang="en">
<head>
<meta charset="utf-8">
<title>Velmont Estates — Business Card</title>
<link href="https://fonts.googleapis.com/css2?family=Open+Sans:wght@400;700&display=swap" rel="stylesheet">
<style>
  :root {
    --backdrop: #e4e6ea;
    --card-white: #ffffff;
    --card-shade: #e9e9ea;
    --turquoise: #14c6c4;
    --grey-soft: rgba(128,128,128,0.45);
    --logo-grey: #7b7b7b;
    --ink: #1e1e1e;
    --ink-on-teal: #17393a;
  }
  * { box-sizing: border-box; margin: 0; padding: 0; }
  html, body { width: 1200px; height: 866px; overflow: hidden; }
  body {
    background: var(--backdrop);
    font-family: "Open Sans", Arial, sans-serif;
    position: relative;
  }
  .card {
    position: absolute;
    width: 520px;
    height: 300px;
    border-radius: 4px;
    overflow: hidden;
    box-shadow: 0 6px 18px rgba(0,0,0,0.12);
  }
  .card-front {
    left: 50px; top: 283px;
    background: radial-gradient(ellipse at 50% 45%, var(--card-white) 0%, #f1f1f2 70%, var(--card-shade) 100%);
    display: flex; align-items: center; justify-content: center;
  }
  .card-back {
    left: 630px; top: 283px;
    background: linear-gradient(135deg, var(--card-shade) 0%, var(--card-white) 45%, #f2f2f3 100%);
  }
  .card-decoration {
    position: absolute; inset: 0;
    background: linear-gradient(115deg, transparent 44%, var(--grey-soft) 50%, var(--turquoise) 58%, var(--turquoise) 100%);
  }

  .brand { display: flex; align-items: center; gap: 14px; position: relative; }
  .brand-mark { background: var(--turquoise); flex: none; }
  .brand-name { font-weight: 400; color: var(--logo-grey); line-height: 1; }
  .brand-name .word-main { display: block; }
  .brand-name .word-sub { display: block; text-transform: uppercase; }

  .card-front .brand-mark { width: 78px; height: 78px; }
  .card-front .word-main { font-size: 52px; letter-spacing: -0.5px; }
  .card-front .word-sub { font-size: 17px; letter-spacing: 7px; margin-top: 6px; }

  .card-back .brand { position: absolute; left: 28px; top: 52px; gap: 10px; }
  .card-back .brand-mark { width: 50px; height: 50px; }
  .card-back .word-main { font-size: 32px; }
  .card-back .word-sub { font-size: 11px; letter-spacing: 4.5px; margin-top: 4px; }

  .holder { position: absolute; left: 28px; top: 128px; color: var(--ink); }
  .holder-name { font-size: 15px; font-weight: 700; }
  .holder-role { font-size: 14px; font-weight: 400; }

  .contact {
    position: absolute; right: 22px; top: 118px;
    list-style: none; text-align: right;
    color: var(--ink-on-teal); font-size: 11px; line-height: 15.5px;
  }
  .contact li { display: flex; justify-content: flex-end; align-items: center; gap: 4px; }
  .contact svg { width: 10px; height: 10px; fill: var(--ink-on-teal); flex: none; }
</style>
</head>
<body>

<section class="card card-front" aria-label="Card front">
  <div class="brand">
    <div class="brand-mark"></div>
    <div class="brand-name">
      <span class="word-main">Velmont</span>
      <span class="word-sub">Estates</span>
    </div>
  </div>
</section>

<section class="card card-back" aria-label="Card back">
  <div class="card-decoration" role="img" aria-label="Decorative teal and grey wave sweeping across the right side"></div>

  <div class="brand">
    <div class="brand-mark"></div>
    <div class="brand-name">
      <span class="word-main">Velmont</span>
      <span class="word-sub">Estates</span>
    </div>
  </div>

  <div class="holder">
    <p class="holder-name">Elin Marsworth</p>
    <p class="holder-role">Consultant</p>
  </div>

  <ul class="contact">
    <li>12th floor, Arden Plaza</li>
    <li>Kessler Road BKK</li>
    <li>021 468 3570
      <svg viewBox="0 0 10 10"><path d="M2 0.5 L3.6 2.6 L2.8 3.6 C3.4 5 4.6 6.3 6 7 L7 6.2 L9.5 7.8 L8.6 9.5 C4.5 9.3 0.8 5.5 0.5 1.4 Z"/></svg>
    </li>
    <li>021 468 3571
      <svg viewBox="0 0 10 10"><rect x="2" y="0.5" width="6" height="3"/><rect x="0.5" y="4" width="9" height="4.5" rx="0.8"/><rect x="2.5" y="7" width="5" height="2.5"/></svg>
    </li>
    <li>elin@velmontestates.asia
      <svg viewBox="0 0 10 10"><path d="M0.5 2 H9.5 V8.5 H0.5 Z M1 2.5 L5 5.6 L9 2.5" stroke="var(--turquoise)" stroke-width="0.7"/></svg>
    </li>
    <li>www.velmontestates.asia</li>
  </ul>
</section>

</body>
</html>
```